Business card design for Automotive workshop

We need a business card for a new automotive repair and tyre shop called Keelstone Prime Automotive located in New Zealand. We are a clean, modern and fresh workshop and company.

Front needs to feature logo,
my name:
Marlo Fenwicke (director)

Address:
48 Tarn Lane
Harrowmere 3590

Phone: 07 594 2713
Mobile: 027 451 9362
Email: office@keelstoneautomotive.example.nz
Website: keelstoneautomotive.example.nz

Back needs to feature an area to write down appointment details, date and time.

Also feature a list of jobs and work we do such as,
Vehicle Servicing
All Mechanical Repairs
Warrant of Fitness
Tyres & Wheel Alignments
Automotive Diagnostics
Automotive Parts & Supplies

```html
<!DOCTYPE html>
<html lang="en">
<head>
<meta charset="utf-8">
<title>Keelstone Prime Automotive – Business Card</title>
<link href="https://fonts.googleapis.com/css2?family=Exo+2:wght@400;500;700&display=swap" rel="stylesheet">
<style>
  :root {
    --bg: #2b2d30;
    --ink: #0b0b0c;
    --red: #e3141c;
    --white: #ffffff;
    --grey: #c9c9c9;
    --dash: #6b6b6b;
  }
  * { box-sizing: border-box; margin: 0; padding: 0; }
  html, body { width: 1200px; height: 900px; overflow: hidden; }
  body {
    background: var(--bg);
    font-family: "Exo 2", sans-serif;
    display: flex;
    flex-direction: column;
    align-items: center;
    justify-content: center;
    gap: 60px;
  }
  .card {
    position: relative;
    width: 660px;
    height: 377px;
    overflow: hidden;
    box-shadow: 0 14px 30px rgba(0,0,0,.45);
  }
  .card-shapes { position: absolute; inset: 0; width: 100%; height: 100%; }
  .card-front { background: var(--ink); color: var(--white); }
  .card-back { background: var(--white); color: var(--ink); }

  .brand {
    position: absolute;
    color: var(--red);
    font-weight: 700;
    text-transform: uppercase;
    letter-spacing: 1px;
    line-height: 1.05;
    display: flex;
    align-items: center;
    gap: 10px;
  }
  .brand-mark { width: 14px; height: 14px; background: var(--red); flex: none; }
  .card-front .brand { left: 40px; top: 42px; font-size: 26px; }
  .card-back .brand { right: 34px; top: 24px; font-size: 24px; flex-direction: row-reverse; text-align: right; }

  .holder { position: absolute; left: 40px; top: 128px; }
  .holder-name { color: var(--red); font-size: 22px; font-weight: 700; letter-spacing: 1.5px; text-transform: uppercase; }
  .holder-role { color: var(--grey); font-size: 14px; }

  .contact-list { position: absolute; left: 40px; top: 192px; list-style: none; font-size: 14px; line-height: 23px; }
  .contact-list li { display: flex; align-items: center; gap: 8px; }
  .contact-list svg { width: 13px; height: 13px; flex: none; }
  .address { position: absolute; left: 40px; top: 300px; font-size: 15px; }

  .service-list { position: absolute; list-style: none; font-size: 13px; font-weight: 500; text-transform: uppercase; line-height: 18px; letter-spacing: .4px; }
  .service-list li { display: flex; align-items: center; gap: 7px; }
  .service-list li::before { content: ""; width: 7px; height: 7px; border-radius: 50%; background: var(--red); flex: none; }
  .services-left { left: 34px; top: 48px; }
  .services-right { right: 30px; top: 158px; text-align: right; }
  .services-right li { flex-direction: row-reverse; }

  .write-line { position: absolute; border-bottom: 1.5px dashed var(--dash); height: 0; }
  .field-label { position: absolute; color: var(--red); font-size: 13px; text-transform: uppercase; }
</style>
</head>
<body>

<section class="card card-front" aria-label="Business card front">
  <svg class="card-shapes" viewBox="0 0 660 377" aria-hidden="true">
    <polygon points="0,0 120,0 0,34" fill="var(--white)"/>
    <polygon points="264,377 660,20 660,377" fill="var(--white)"/>
    <polygon points="460,377 660,200 660,377" fill="var(--red)"/>
  </svg>
  <div class="brand"><span class="brand-mark"></span><span>Keelstone Prime<br>Automotive</span></div>
  <div class="holder">
    <p class="holder-name">Marlo Fenwicke</p>
    <p class="holder-role">Director</p>
  </div>
  <ul class="contact-list">
    <li><svg viewBox="0 0 16 16"><circle cx="8" cy="8" r="7" fill="none" stroke="#fff" stroke-width="1.3"/><path d="M5 4.5l1.5 0 .7 2-1 .8a5 5 0 0 0 2.5 2.5l.8-1 2 .7v1.5c-3.5.3-6.8-3-6.5-6.5z" fill="#fff"/></svg>07 594 2713</li>
    <li><svg viewBox="0 0 16 16"><rect x="4" y="1" width="8" height="14" rx="1.5" fill="none" stroke="#fff" stroke-width="1.4"/><circle cx="8" cy="12.5" r=".9" fill="#fff"/></svg>027 451 9362</li>
    <li><svg viewBox="0 0 16 16"><rect x="1" y="3" width="14" height="10" fill="none" stroke="#fff" stroke-width="1.3"/><path d="M1 3l7 6 7-6" fill="none" stroke="#fff" stroke-width="1.3"/></svg>office@keelstoneautomotive.example.nz</li>
    <li><svg viewBox="0 0 16 16"><circle cx="8" cy="8" r="7" fill="none" stroke="#fff" stroke-width="1.3"/><ellipse cx="8" cy="8" rx="3" ry="7" fill="none" stroke="#fff" stroke-width="1.1"/><path d="M1 8h14" stroke="#fff" stroke-width="1.1"/></svg>keelstoneautomotive.example.nz</li>
  </ul>
  <p class="address">48 Tarn Lane, Harrowmere 3590</p>
</section>

<section class="card card-back" aria-label="Business card back">
  <svg class="card-shapes" viewBox="0 0 660 377" aria-hidden="true">
    <polygon points="0,0 160,0 0,36" fill="var(--red)"/>
    <polygon points="215,0 660,0 660,150 330,58" fill="var(--ink)"/>
    <polygon points="0,215 0,245 190,377 160,377" fill="var(--red)"/>
    <polygon points="0,245 190,377 0,377" fill="var(--ink)"/>
  </svg>
  <div class="brand"><span class="brand-mark"></span><span>Keelstone Prime<br>Automotive</span></div>
  <ul class="service-list services-left">
    <li>Vehicle Servicing</li>
    <li>All Mechanical Repairs</li>
    <li>Warrant of Fitness</li>
  </ul>
  <ul class="service-list services-right">
    <li>Tyres &amp; Wheel Alignments</li>
    <li>Automotive Diagnostics</li>
    <li>Automotive Parts &amp; Supplies</li>
  </ul>
  <span class="field-label" style="left:34px; top:162px;">Date:</span>
  <div class="write-line" style="left:34px; top:130px; width:330px;"></div>
  <div class="write-line" style="left:80px; top:178px; width:284px;"></div>
  <div class="write-line" style="left:34px; top:236px; width:596px;"></div>
  <span class="field-label" style="left:210px; top:280px;">Time:</span>
  <div class="write-line" style="left:256px; top:296px; width:374px;"></div>
  <div class="write-line" style="left:210px; top:346px; width:420px;"></div>
</section>

</body>
</html>
```